Shipping and Logistics, Project

Project description : Company Profile

A total logistics company covering domestic / international freight forwarding, warehouse management services, haulage, supply chain management, transport management & distribution, procurement & assembly services, shipping, chartering & bunker services, project logistics & tax exemption consultancy, oil & gas logistics, halal logistics services & integrated logistics management. We’re a well-established and experienced freight forwarder in Kuala Lumpur, Malaysia. We specialize in customized value-added solution that optimizes your supply chain by trimming inventory, reducing logistics cost and enhancing your customer service levels.

As a member of the Worldwide Parcel and Carriage Alliance which comprise of 170 global freight agents in 80 countries that promotes great handling in cross-trade logistics and freighting. You could rely on our efficiency in handlings of export cargo (FCL, LCL, Bulk and Conventional) between our global network offices worldwide with a total scale of 10,000 groomed specialists in various logistics division working together to ensure delivery task meets with your expectation. With our dedicated qualified and experienced professionals, we are fully committed to serving our clients.

Our generic services are listed below for your reference:

• Air Freight
• Ocean Freight FCL & LCL
• Container Haulage
• Warehousing
• Transportation and Distribution within Malaysia and Thailand
• Cross-Border Road Line-hauls between Thailand, Malaysia, Singapore and Laos
• Customs Brokerage and Forwarding
• Project Cargo Freight Forwarding for setting up of new plants / factories and ad hoc heavy-lift
• Air-Sea-Road-Rail multi-modal options
• Import / Export / Storage / Documentation / Handling of DG / Hazmat
• Vessel and Aircraft Charters

Our Mission
Based on the motto “Quick, Reliable and Polite”, we are dedicated to upholding the following three points corporate philosophy:
1. Adhering to the principle that “the customer always comes first”.
2. Contributing to the development of the local community.
3. Making it our duty to be responsible and sincere.

Our Edge
• One-Stop Logistics Solutions
• Extensive Network Throughout Malaysia
• Highly Qualified and Experienced Pool of Professionals
• Comprehensive IT Solutions
• Innovative and Customer-focused Solutions
• Flexible and Consistent in Managing Exceptions
• Total Supply Chain Visibility

Target Market
1. We sell the logistics services to all the industry in Malaysia and Worldwide. (ONE Stop Logistics Solutions)

Competitor
1. TR Valmont
2. Corvessa Transport
3. Brandt + Loewe
4. FELRO
5. QTV
6. Routemarks
7. Ilto Logistics

Rules for Picking a Company Name
1. Unique and unforgettable
2. Avoid unusual spellings
3. Easy to pronounce and remember
4. Keep it simple
5. Make some sense
6. Give a clue

Rules for Picking a Company Logo
4. Keep it simple
5. Make some sense
6. Give a clue

1. Simplicity
2. Memorability
3. Originality
4. Modern Yet Timeless
5. Balance
6. Complementary
7. Versatility

Stationery Information
1. Company Name : ZENFreight Solutions Sdn Bhd
2. Company Registration : 2837165-W
3. Address : 42-08, Jalan Cempaka Indah 5, Taman Seri Bayu, 81300 Johor Bahru, Johor, Malaysia.
4. Name : Derek Tan
5. Position : Manager
6. Mobile No : (+6019) 4381907
7. Office No : (+607) 5218764
8. Fax No : Not Available
9. Email Address : derek.tan@zenfreight-solutions.example
10. Web Domain : www.zenfreight-solutions.example
11. Company Slogan : Moving the World Onward

Target Market(s)

Corporate Company

Industry/Entity Type

Shipping and Logistics Industry

Requirements
Must have
• Company Full Name : ZENFREIGHT SOLUTIONS SDN. BHD.
Nice to have
• Keep it simple and unforgettable ...

```html
<!DOCTYPE html>
<html lang="en">
<head>
<meta charset="utf-8">
<title>ZENFreight Solutions – Business Card</title>
<link rel="stylesheet" href="https://fonts.googleapis.com/css2?family=Montserrat:wght@400;600;700&family=Open+Sans:wght@400;600&display=swap">
<style>
  :root {
    --stage: #1a1a1a;
    --card: #262626;
    --brand-blue: #2e8bdc;
    --ink-light: #ffffff;
    --ink-muted: #e6e6e6;
  }
  * { box-sizing: border-box; margin: 0; padding: 0; }
  html, body {
    width: 1200px; height: 1015px; overflow: hidden;
    background: var(--stage);
  }
  .stage { position: relative; width: 1200px; height: 1015px; }
  .card {
    position: absolute; width: 560px; height: 320px;
    background: var(--card); overflow: hidden;
    box-shadow: 0 18px 40px rgba(0,0,0,.55);
  }

  /* Front */
  .card--front { left: 170px; top: 120px; font-family: "Montserrat", sans-serif; }
  .registration {
    position: absolute; top: 42px; left: 0; right: 0; text-align: center;
    font-size: 12px; color: var(--ink-light); letter-spacing: .5px;
  }
  .registration__number { color: var(--brand-blue); }
  .brand {
    position: absolute; top: 118px; left: 0; right: 0;
    display: flex; align-items: center; justify-content: center; gap: 18px;
  }
  .brand__square {
    width: 62px; height: 62px; border: 5px solid var(--brand-blue);
  }
  .brand__name {
    font-weight: 700; color: var(--ink-light); line-height: 1.1;
    letter-spacing: 2px;
  }
  .brand__name-main { display: block; font-size: 38px; letter-spacing: 3px; }
  .brand__name-sub { display: block; font-size: 13px; letter-spacing: 3.4px; margin-top: 4px; }
  .slogan {
    position: absolute; bottom: 46px; left: 0; right: 0; text-align: center;
    font-size: 13px; font-weight: 600; letter-spacing: 1.5px; color: var(--brand-blue);
  }

  /* Back */
  .card--back { left: 470px; top: 555px; font-family: "Open Sans", sans-serif; }
  .card__band {
    position: absolute; inset: 0; background: var(--brand-blue);
    clip-path: polygon(58% 0, 100% 0, 100% 100%, 80% 100%);
  }
  .holder { position: absolute; left: 40px; top: 44px; }
  .holder__name {
    font-family: "Montserrat", sans-serif; font-weight: 700; font-size: 26px;
    color: var(--brand-blue); letter-spacing: 1px; line-height: 1;
  }
  .holder__role { font-size: 14px; color: var(--ink-light); margin-top: 4px; }
  .address {
    position: absolute; left: 40px; top: 132px;
    font-size: 13px; line-height: 1.35; color: var(--ink-muted); font-style: normal;
  }
  .contact-list {
    position: absolute; left: 40px; top: 222px; list-style: none;
    font-size: 13px; line-height: 1.55; color: var(--ink-muted);
  }
  .contact-list li { display: flex; align-items: center; gap: 8px; }
  .contact-list svg { width: 13px; height: 13px; flex: none; }
  .icon { fill: none; stroke: var(--brand-blue); stroke-width: 1.8; }
</style>
</head>
<body>
<main class="stage">

  <section class="card card--front" aria-label="Card front">
    <p class="registration">Registration : <span class="registration__number">2837165-W</span></p>
    <div class="brand">
      <span class="brand__square" aria-hidden="true"></span>
      <p class="brand__name">
        <span class="brand__name-main">ZENFREIGHT</span>
        <span class="brand__name-sub">SOLUTIONS SDN. BHD.</span>
      </p>
    </div>
    <p class="slogan">MOVING THE WORLD ONWARD</p>
  </section>

  <section class="card card--back" aria-label="Card back">
    <div class="card__band" aria-hidden="true"></div>
    <div class="holder">
      <h1 class="holder__name">DEREK TAN</h1>
      <p class="holder__role">Manager</p>
    </div>
    <address class="address">
      42-08, Jalan Cempaka Indah 5<br>
      Taman Seri Bayu<br>
      81300 Johor Bahru<br>
      Johor, Malaysia
    </address>
    <ul class="contact-list">
      <li>
        <svg viewBox="0 0 14 14" aria-hidden="true"><rect class="icon" x="3" y="1" width="8" height="12" rx="1.5"/></svg>
        (+6019) 4381907
      </li>
      <li>
        <svg viewBox="0 0 14 14" aria-hidden="true"><path class="icon" d="M3 1.5l2.5 2.5-1.5 1.5c1 2 2.5 3.5 4.5 4.5L10 8.5l2.5 2.5-2 2C6 12.5 1.5 8 1 3.5z"/></svg>
        (+607) 5218764
      </li>
      <li>
        <svg viewBox="0 0 14 14" aria-hidden="true"><rect class="icon" x="1" y="3" width="12" height="8"/><path class="icon" d="M1 3l6 5 6-5"/></svg>
        derek.tan@zenfreight-solutions.example
      </li>
      <li>
        <svg viewBox="0 0 14 14" aria-hidden="true"><circle class="icon" cx="7" cy="7" r="5.8"/><path class="icon" d="M1.2 7h11.6M7 1.2c-3 3.5-3 8.1 0 11.6M7 1.2c3 3.5 3 8.1 0 11.6"/></svg>
        www.zenfreight-solutions.example
      </li>
    </ul>
  </section>

</main>
</body>
</html>
```